Verodex business card

Business card for sustainable investment company called "Verodex". Verodex is an exchange platform selling carbon credits between buyers and sellers. Carbon Credits are an environmental commodity for reducing global carbon emissions.

the card should obviously have our logo and the theme should be sustainability/environment mixed with a trading platform.

Contact Information for Business Card

Logo, Name, Title, Phone, Email

Colors
0054AA
0677BA
7BADD7
CADEEF
E8F1F8
0094D4
00A9DD
6FCCEA
C7EBF8
E9F6FB
00AB8E
00BBA5
67D7C9
C6EFE9
E9F9F6
59FF00
82FF00
B8FF75
E3FFCB
F4FFEA

```html
<!DOCTYPE html>
<html lang="en">
<head>
<meta charset="utf-8">
<title>Verodex business card</title>
<link href="https://fonts.googleapis.com/css2?family=Poppins:wght@400;500;600;700&display=swap" rel="stylesheet">
<style>
  :root {
    --backdrop: #1e1f21;
    --card-white: #ffffff;
    --card-black: #0f1012;
    --navy: #1b2c4b;
    --ink: #1a1a1a;
    --rule: #9a9a9a;
    --brand-blue: #1a8fe6;
    --brand-cyan: #19b6ea;
    --pattern-light: #5d5f63;
    --pattern-dark: #141517;
  }
  * { box-sizing: border-box; margin: 0; padding: 0; }
  html, body {
    width: 1200px;
    height: 1108px;
    overflow: hidden;
    background: var(--backdrop);
    font-family: "Poppins", sans-serif;
  }
  .stage {
    position: relative;
    width: 1200px;
    height: 1108px;
  }
  .card {
    position: absolute;
    top: 264px;
    width: 340px;
    height: 580px;
    border-radius: 22px;
    overflow: hidden;
  }
  .card-front {
    left: 200px;
    background: var(--card-white);
    color: var(--navy);
  }
  .card-back {
    left: 660px;
    background: var(--card-black);
  }

  /* front */
  .brand {
    position: absolute;
    top: 96px;
    left: 0;
    right: 0;
    display: flex;
    align-items: center;
    justify-content: center;
    gap: 14px;
  }
  .brand-square {
    width: 44px;
    height: 44px;
    background: var(--brand-blue);
    border-radius: 4px;
  }
  .brand-name {
    font-weight: 600;
    font-size: 40px;
    letter-spacing: 1px;
    color: var(--navy);
    line-height: 1;
  }
  .person {
    position: absolute;
    top: 360px;
    left: 0;
    right: 0;
    text-align: center;
  }
  .person-name {
    font-weight: 700;
    font-size: 25px;
    letter-spacing: 1px;
    line-height: 1.1;
  }
  .person-title {
    font-weight: 400;
    font-size: 15px;
    letter-spacing: 0.5px;
    margin-top: 2px;
  }
  .icon-row {
    position: absolute;
    top: 434px;
    left: 28px;
    right: 28px;
    display: flex;
    align-items: center;
    gap: 8px;
  }
  .icon-row .rule {
    flex: 1;
    height: 1px;
    background: var(--rule);
  }
  .icon {
    width: 26px;
    height: 26px;
    border-radius: 4px;
    background: var(--navy);
    display: flex;
    align-items: center;
    justify-content: center;
  }
  .contacts {
    position: absolute;
    top: 472px;
    left: 0;
    right: 0;
    text-align: center;
    list-style: none;
    color: var(--ink);
    font-size: 16px;
    line-height: 1.45;
  }

  /* back */
  .back-pattern {
    position: absolute;
    inset: 0;
    background: linear-gradient(200deg, var(--pattern-light) 0%, #2e3033 40%, var(--pattern-dark) 75%, #0b0c0d 100%);
  }
  .back-brand {
    position: absolute;
    left: 0;
    right: 0;
    top: 430px;
    text-align: center;
    font-weight: 600;
    font-size: 24px;
    letter-spacing: 1px;
    color: var(--brand-blue);
  }
</style>
</head>
<body>
<main class="stage">
  <section class="card card-front" aria-label="Card front">
    <div class="brand">
      <span class="brand-square" aria-hidden="true"></span>
      <span class="brand-name">VERODEX</span>
    </div>

    <div class="person">
      <p class="person-name">MARCUS HALE</p>
      <p class="person-title">MANAGING DIRECTOR</p>
    </div>

    <div class="icon-row">
      <span class="rule"></span>
      <span class="icon" aria-label="Phone">
        <svg width="16" height="16" viewBox="0 0 24 24" fill="#fff"><path d="M6.6 10.8a15 15 0 0 0 6.6 6.6l2.2-2.2c.3-.3.7-.4 1-.2 1.1.4 2.3.6 3.6.6.6 0 1 .4 1 1V20c0 .6-.4 1-1 1A17 17 0 0 1 3 4c0-.6.4-1 1-1h3.5c.6 0 1 .4 1 1 0 1.3.2 2.5.6 3.6.1.3 0 .7-.2 1z"/></svg>
      </span>
      <span class="icon" aria-label="Email">
        <svg width="16" height="16" viewBox="0 0 24 24" fill="none" stroke="#fff" stroke-width="2"><rect x="3" y="5" width="18" height="14" rx="1"/><path d="M3 6l9 7 9-7"/></svg>
      </span>
      <span class="icon" aria-label="Website">
        <svg width="16" height="16" viewBox="0 0 24 24" fill="none" stroke="#fff" stroke-width="2"><circle cx="12" cy="12" r="9"/><path d="M3 12h18M12 3c3 3 3 15 0 18M12 3c-3 3-3 15 0 18"/></svg>
      </span>
      <span class="rule"></span>
    </div>

    <ul class="contacts">
      <li>044-987 654 321</li>
      <li>info@verodexmail.com</li>
      <li>www.verodexsite.com</li>
    </ul>
  </section>

  <section class="card card-back" aria-label="Card back">
    <div class="back-pattern" role="img" aria-label="Repeating glossy brand pattern fading from silver to black across the card"></div>
    <p class="back-brand">VERODEX</p>
  </section>
</main>
</body>
</html>
```